Need a Basketball Court Design

We are replacing our current basketball court (gym floor) and we are looking for a new design. Our team is the “Larkmoor Falcons”. Our mascot is a “Knight” (in shining armor). Our colors are royal blue/grey/black. We are looking for a design that is contemporary and energetic.
The background of the court should display a “castle”. In the center of the court should be a team logo. You can use one of our existing logos or create your own. Along the baseline of the court should read the word “Larkmoor”.
I’ve attached ...
1) a picture of the current court
2) a mock-up design of what we are thinking
3) some of the different team logos we use.

```html
<!DOCTYPE html>
<html lang="en">
<head>
<meta charset="UTF-8">
<title>Larkmoor Basketball Court</title>
<link href="https://fonts.googleapis.com/css2?family=Alfa+Slab+One&family=Oswald:wght@700&display=swap" rel="stylesheet">
<style>
  :root {
    --frame-black: #050505;
    --royal-blue: #264f9c;
    --wood-light: #f0cf9f;
    --wood-mid: #e2b47d;
    --wood-dark: #d49c5f;
    --line-white: #ffffff;
    --castle-shade: rgba(95, 80, 60, 0.72);
  }
  html, body {
    margin: 0;
    padding: 0;
    width: 1200px;
    height: 600px;
    overflow: hidden;
    background: #ffffff;
  }
  .court-canvas {
    display: block;
    width: 1200px;
    height: 600px;
  }
  .side-word {
    font-family: "Alfa Slab One", Georgia, serif;
    font-size: 50px;
    fill: var(--royal-blue);
  }
  .baseline-slogan {
    font-family: "Oswald", "Arial Narrow", sans-serif;
    font-weight: 700;
    font-size: 31px;
    letter-spacing: 7px;
    fill: var(--line-white);
  }
  .center-name {
    font-family: "Alfa Slab One", Georgia, serif;
    font-size: 25px;
    fill: var(--royal-blue);
  }
  .corner-name {
    font-family: "Alfa Slab One", Georgia, serif;
    font-size: 18px;
    fill: var(--royal-blue);
  }
  .court-line {
    fill: none;
    stroke: var(--line-white);
    stroke-width: 2.5;
  }
</style>
</head>
<body>
<svg class="court-canvas" viewBox="0 0 1200 600" xmlns="http://www.w3.org/2000/svg">
  <defs>
    <linearGradient id="wood-floor" x1="0" y1="0" x2="1" y2="1">
      <stop offset="0" stop-color="var(--wood-light)"/>
      <stop offset="0.5" stop-color="var(--wood-mid)"/>
      <stop offset="1" stop-color="var(--wood-dark)"/>
    </linearGradient>
  </defs>

  <!-- outer frame -->
  <rect class="frame" x="67" y="13" width="1077" height="574" fill="var(--frame-black)"/>

  <!-- playing surface -->
  <rect class="floor" x="134" y="50" width="940" height="498" fill="url(#wood-floor)"/>

  <!-- castle backdrop area -->
  <rect class="castle-backdrop" role="img" aria-label="Castle silhouette with towers and a flag spanning centre court"
        x="318" y="185" width="577" height="363" fill="var(--castle-shade)"/>

  <!-- left half court -->
  <g class="half-court half-court--left">
    <rect class="paint" x="134" y="238" width="179" height="118" fill="var(--royal-blue)"/>
    <path d="M313 238 A60 59 0 0 0 313 356 Z" fill="var(--frame-black)"/>
    <path class="court-line" d="M313 238 A60 59 0 0 1 313 356"/>
    <path class="court-line" d="M313 238 A60 59 0 0 0 313 356"/>
    <line class="court-line" x1="134" y1="238" x2="313" y2="238"/>
    <line class="court-line" x1="134" y1="356" x2="313" y2="356"/>
    <line class="court-line" x1="313" y1="238" x2="313" y2="356"/>
    <path class="court-line" d="M200 238 v-6 M228 238 v-6 M257 238 v-6 M286 238 v-6 M200 356 v6 M228 356 v6 M257 356 v6 M286 356 v6"/>
    <line class="court-line" x1="166" y1="262" x2="166" y2="333"/>
    <circle class="court-line" cx="187" cy="297" r="18"/>
    <path class="court-line" d="M134 101 H195 A192 197 0 0 1 195 497 H134"/>
    <text class="corner-name" x="215" y="430" text-anchor="middle">LARKMOOR</text>
  </g>

  <!-- right half court (mirrored) -->
  <g class="half-court half-court--right" transform="translate(1208 0) scale(-1 1)">
    <rect class="paint" x="134" y="238" width="179" height="118" fill="var(--royal-blue)"/>
    <path d="M313 238 A60 59 0 0 0 313 356 Z" fill="var(--frame-black)"/>
    <path class="court-line" d="M313 238 A60 59 0 0 1 313 356"/>
    <path class="court-line" d="M313 238 A60 59 0 0 0 313 356"/>
    <line class="court-line" x1="134" y1="238" x2="313" y2="238"/>
    <line class="court-line" x1="134" y1="356" x2="313" y2="356"/>
    <line class="court-line" x1="313" y1="238" x2="313" y2="356"/>
    <path class="court-line" d="M200 238 v-6 M228 238 v-6 M257 238 v-6 M286 238 v-6 M200 356 v6 M228 356 v6 M257 356 v6 M286 356 v6"/>
    <line class="court-line" x1="166" y1="262" x2="166" y2="333"/>
    <circle class="court-line" cx="187" cy="297" r="18"/>
    <path class="court-line" d="M134 101 H195 A192 197 0 0 1 195 497 H134"/>
  </g>
  <text class="corner-name" x="1000" y="178" text-anchor="middle">LARKMOOR</text>

  <!-- half-court line -->
  <line class="court-line" x1="605" y1="50" x2="605" y2="548"/>

  <!-- court boundary -->
  <rect class="court-line" x="134" y="50" width="940" height="498"/>

  <!-- centre circle with team name -->
  <g class="center-mark">
    <circle cx="605" cy="296" r="102" fill="var(--frame-black)" stroke="var(--line-white)" stroke-width="4"/>
    <text class="center-name" x="605" y="305" text-anchor="middle">LARKMOOR</text>
  </g>

  <!-- sideline wordmarks -->
  <text class="side-word" transform="translate(122 300) rotate(-90)" text-anchor="middle" letter-spacing="14">LARKMOOR</text>
  <text class="side-word" transform="translate(1090 300) rotate(90)" text-anchor="middle" letter-spacing="6">BASKETBALL</text>

  <!-- baseline slogan -->
  <text class="baseline-slogan" x="615" y="582" text-anchor="middle">WELCOME TO THE HIGH TOWER</text>
</svg>
</body>
</html>
```